Business Card Design

Business Card for professional consulting firm working with large financial institutions.

Target Market(s)

Executive buyers

Industry/Entity Type

Banking

Contact Information for Business Card

Mild creativity wanted. Not boring, but do elaborate artwork.

Font styles to use
Serif
Sans Serif

Colors

Designer to choose colors to be used in the design.

Requirements
Must have
• Standard business card features - company name, individual name, telephone, website, email, locations.
Nice to have
• Two colors
Should not have
• too many colors, fancy printing, cartoons.

```html
<!DOCTYPE html>
<html lang="en">
<head>
<meta charset="UTF-8">
<title>Harlow Advisory Business Card</title>
<link href="https://fonts.googleapis.com/css2?family=Roboto:wght@400;500;700&display=swap" rel="stylesheet">
<style>
  :root {
    --page-bg: #e9e6e1;
    --card-paper: #f1f1f1;
    --front-frame: #000000;
    --back-frame: #c4c4c4;
    --ink: #111111;
    --ink-soft: #4a4a4a;
    --ink-muted: #a9a9a9;
    --rule: #cfcfcf;
  }
  * { margin: 0; padding: 0; box-sizing: border-box; }
  html, body { width: 1200px; height: 960px; overflow: hidden; }
  body { background: var(--page-bg); position: relative; font-family: "Roboto", Arial, sans-serif; }

  .card { position: absolute; box-shadow: 0 3px 6px rgba(0,0,0,0.35); }
  .card-front { left: 314px; top: 113px; width: 600px; height: 343px; background: var(--front-frame); }
  .card-back  { left: 312px; top: 472px; width: 599px; height: 343px; background: var(--back-frame); }
  .card-face { position: absolute; background: var(--card-paper); }
  .card-front .card-face { left: 13px; top: 13px; width: 574px; height: 316px; }
  .card-back .card-face  { left: 12px; top: 14px; width: 574px; height: 315px; }

  .company-name {
    position: absolute; font-family: "Roboto", Arial, sans-serif; font-weight: 400;
    color: var(--ink); white-space: nowrap; text-align: center; letter-spacing: 0.3px;
  }
  .card-front .company-name { left: 20px; width: 280px; top: 137px; font-size: 27px; line-height: 34px; }
  .card-back .company-name { left: 0; right: 0; top: 131px; font-size: 33px; line-height: 40px; }

  .divider { position: absolute; left: 322px; top: 79px; width: 1px; height: 163px; background: var(--rule); }

  .contact-block { position: absolute; left: 352px; top: 79px; }
  .person-name { font-size: 20px; font-weight: 700; color: var(--ink); letter-spacing: 0.3px; line-height: 24px; }
  .person-title { font-size: 14.5px; font-weight: 500; color: var(--ink-muted); line-height: 18px; }
  .address { margin-top: 12px; font-size: 14.5px; color: var(--ink-soft); line-height: 19px; }
  .contact-list { list-style: none; margin-top: 9px; }
  .contact-list li { display: flex; align-items: center; gap: 8px; font-size: 14.5px; color: var(--ink-soft); line-height: 19.5px; }
  .contact-list svg { width: 13px; height: 13px; fill: var(--ink); flex: none; }
</style>
</head>
<body>
  <section class="card card-front">
    <div class="card-face">
      <div class="company-name">Harlow Advisory</div>
      <div class="divider"></div>
      <div class="contact-block">
        <div class="person-name">DANIEL REED</div>
        <div class="person-title">CEO/FOUNDER</div>
        <div class="address">4120 Juniper Court<br>Fairbanks, Alaska 99701</div>
        <ul class="contact-list">
          <li>
            <svg viewBox="0 0 24 24" aria-hidden="true"><path d="M6.6 10.8c1.4 2.8 3.8 5.1 6.6 6.6l2.2-2.2c.3-.3.7-.4 1-.2 1.1.4 2.3.6 3.6.6.6 0 1 .4 1 1V20c0 .6-.4 1-1 1C10.6 21 3 13.4 3 4c0-.6.4-1 1-1h3.5c.6 0 1 .4 1 1 0 1.3.2 2.5.6 3.6.1.3 0 .7-.2 1L6.6 10.8z"/></svg>
            <span>555 214 7730</span>
          </li>
          <li>
            <svg viewBox="0 0 24 24" aria-hidden="true"><path d="M2 5h20v2.2l-10 6.6L2 7.2z"/><path d="M2 9.5l10 6.4 10-6.4V19H2z"/></svg>
            <span>info@harlowadvisory.com</span>
          </li>
          <li>
            <svg viewBox="0 0 24 24" aria-hidden="true"><circle cx="12" cy="12" r="10"/><path d="M7 8c2 0 3 1 3 2.5S8.5 13 9 15s2 2 2 4" fill="none" stroke="#f1f1f1" stroke-width="2"/><path d="M14 5c1 1.5 3 1.5 3.5 3S16 11 17.5 12.5" fill="none" stroke="#f1f1f1" stroke-width="2"/></svg>
            <span>www.harlowadvisory.com</span>
          </li>
        </ul>
      </div>
    </div>
  </section>

  <section class="card card-back">
    <div class="card-face">
      <div class="company-name">Harlow Advisory</div>
    </div>
  </section>
</body>
</html>
```